Food humor T-shirt and apparel company needs a Shopify site designed. We have logo files to help.

We are an apparel company based in Chicago by two cooking and food humor enthusiasts. We are looking for a redesign of our Shopify site. Our products are humorous quotes and pictures on shirts, sweaters and other apparel. The tagline for the company is - Find Your Yum. Wear Your Food. We want to see designs that incorporate our logo, brand color of royal purple, signify fun business casual clothing with amusing tags or images of trendy or esoteric food trends. The design should communicate excellence in taste but with maybe a satirical almost corporate type spin.
Target Market(s)
Hip, millennial foodies and cooks that love to try new foods, have great taste, and love to experiment in the restaurant or the kitchen.
Industry/Entity Type
Cooking
Look and feel
Each slider illustrates characteristics of the customer's brand and the style your logo design should communicate.

```html
<!DOCTYPE html>
<html lang="en">
<head>
<meta charset="utf-8">
<title>Savorly — Find Your Yum. Wear Your Food.</title>
<link href="https://fonts.googleapis.com/css2?family=Poppins:wght@600;700&family=Open+Sans:wght@400;600;700&display=swap" rel="stylesheet">
<style>
:root{
  --purple:#6d46a0;
  --purple-soft:#8a69b5;
  --blue:#0d57a8;
  --lavender:#f1eff6;
  --ink:#222;
  --muted:#777;
  --line:#d6d6d6;
  --footer:#262626;
  --white:#fff;
}
*{box-sizing:border-box;margin:0;padding:0}
html,body{width:1200px;height:4584px;overflow:hidden}
body{font-family:"Open Sans",sans-serif;color:var(--ink);position:relative;background:var(--white)}
section,header,footer{position:absolute;left:0;width:1200px}
.abs{position:absolute}
.photo{position:absolute}
h2.title{position:absolute;left:0;width:1200px;text-align:center;font-family:"Poppins",sans-serif;font-weight:700;font-size:37px;color:var(--ink);letter-spacing:-.5px}

/* hero */
.hero{top:0;height:611px;background:linear-gradient(120deg,#5e5c58,#8b8780 45%,#b4b0a8);overflow:hidden}
.brand{position:absolute;left:110px;top:70px;font-family:"Open Sans",sans-serif;font-weight:700;font-size:27px;color:var(--white)}
.nav{position:absolute;top:50px;left:426px;display:flex;gap:22px;font-size:13.5px;font-weight:600;color:var(--white)}
.nav svg{margin-top:2px}
.hero-head{position:absolute;right:112px;top:240px;text-align:right;font-family:"Poppins",sans-serif;font-weight:700;font-size:46px;line-height:64px;color:var(--white);letter-spacing:-.5px}
.arrow{position:absolute;top:294px}

/* welcome */
.welcome{top:611px;height:559px}
.frame{position:absolute;border:2px solid #e4e4e4;background:var(--white)}
.welcome h1{position:absolute;left:600px;top:138px;font-family:"Poppins",sans-serif;font-weight:700;font-size:37px;line-height:43px;letter-spacing:-.5px}
.welcome p{position:absolute;left:600px;top:248px;width:410px;font-size:15.5px;line-height:27.4px;color:var(--muted)}

/* featured */
.featured{top:1170px;height:584px;background:var(--lavender)}
.product{position:absolute;top:149px;width:232px}
.product .img{height:275px}
.product .label{height:42px;background:var(--purple-soft);color:var(--white);font-size:13px;font-weight:600;text-align:center;line-height:42px}

/* banner */
.banner{top:1754px;height:342px;background:linear-gradient(100deg,#2b3949,#3d5166 45%,#6f8193)}
.banner p{position:absolute;top:184px;width:1200px;text-align:center;color:var(--white);font-size:26px;line-height:35px}

/* testimonials */
.testimonials{top:2096px;height:523px}
.card{position:absolute;top:217px;width:310px;height:196px;border:1.5px solid var(--line);text-align:center}
.avatar{position:absolute;top:-52px;left:110px;width:90px;height:90px;border-radius:50%;background:linear-gradient(#d8d2cc,#a79e96);border:3px solid var(--white)}
.card h3{margin-top:56px;font-size:15.5px;font-weight:600;color:var(--ink)}
.card p{margin:12px auto 0;width:260px;font-size:14px;line-height:26.6px;color:var(--muted)}

/* deal */
.deal{top:2619px;height:632px;background:var(--lavender)}
.deal .info{position:absolute;left:600px;top:194px;font-size:16px}
.sizes{position:absolute;top:112px;display:flex;gap:20px}
.size{height:36px;border:1.5px solid #b5b5b5;font-size:13px;color:var(--muted);line-height:33px;padding:0 13px}
.size.on{background:var(--blue);border-color:var(--blue);color:var(--white);font-weight:700}
.btn{position:absolute;background:var(--blue);color:var(--white);font-size:13.5px;font-weight:700;text-align:center}

/* news */
.news{top:3251px;height:659px}
.news .meta{position:absolute;left:650px;top:230px;font-size:15px;color:var(--muted)}
.news p{position:absolute;left:650px;top:277px;width:440px;font-size:15.5px;line-height:27.4px;color:var(--muted)}

/* subscribe */
.subscribe{top:3910px;height:240px;background:var(--purple)}
.subscribe h2{position:absolute;left:110px;width:440px;top:75px;text-align:center;font-family:"Poppins",sans-serif;font-weight:700;font-size:36px;line-height:42px;color:var(--white)}
.sub-input{position:absolute;left:577px;top:100px;width:379px;height:42px;background:var(--white);font-size:13.5px;color:#999;line-height:42px;padding-left:20px}

/* footer */
.footer{top:4150px;height:434px;background:var(--footer);color:var(--white)}
.footer h4{position:absolute;top:74px;font-size:15px;font-weight:700}
.footer .txt{position:absolute;font-size:13.5px;line-height:27.6px}
.field{position:absolute;left:614px;width:276px;border:1.5px solid #8a8a8a;font-size:13.5px;padding:8px 20px}
.pay{display:inline-block;width:34px;height:22px;border-radius:3px;margin-right:6px}
.social{position:absolute;left:982px;font-size:14px;display:flex;align-items:center;gap:12px}
.social i{width:34px;height:34px;border:1.5px solid #9a9a9a;border-radius:50%;display:block}
</style>
</head>
<body>

<header class="hero">
  <div class="photo" role="img" aria-label="Man in sunglasses wearing a white T-shirt with a gelato print" style="left:0;top:0;width:1200px;height:611px;background:linear-gradient(120deg,#5a5753,#8b8780 45%,#b7b2aa)"></div>
  <div class="brand">Savorly</div>
  <nav class="nav">
    <span>HOME</span><span>SHOP</span><span>ABOUT US</span><span>LOG IN</span><span>CREATE ACCOUNT</span><span>BLOG</span><span>CONTACT</span>
    <svg width="14" height="14" viewBox="0 0 14 14"><circle cx="6" cy="6" r="4.3" fill="none" stroke="#fff" stroke-width="2"/><path d="M9 9l4 4" stroke="#fff" stroke-width="2"/></svg>
    <svg width="14" height="14" viewBox="0 0 14 14"><path d="M0 1h3l2 8h7l2-6H4" fill="none" stroke="#fff" stroke-width="2"/><circle cx="6" cy="12" r="1.4" fill="#fff"/><circle cx="11" cy="12" r="1.4" fill="#fff"/></svg>
  </nav>
  <div class="hero-head">FIND YOUR YUM. WEAR<br>YOUR FOOD.</div>
  <svg class="arrow" style="left:44px" width="14" height="22" viewBox="0 0 14 22"><path d="M11 2L3 11l8 9" fill="none" stroke="#fff" stroke-width="3"/></svg>
  <svg class="arrow" style="left:1143px" width="14" height="22" viewBox="0 0 14 22"><path d="M3 2l8 9-8 9" fill="none" stroke="#fff" stroke-width="3"/></svg>
</header>

<section class="welcome">
  <div class="frame" style="left:110px;top:112px;width:399px;height:335px">
    <div class="photo" role="img" aria-label="Man wearing a black hoodie with a gelato print" style="left:60px;top:0;width:275px;height:331px;background:linear-gradient(#3a332d,#111 40%,#0c0c0c)"></div>
  </div>
  <h1>WELCOME TO<br>SAVORLY</h1>
  <p>Savorly was born from the hearts of two foodies and travelholics based in Los Angeles and Chicago. Savorly is an expression of their mutual love of and wanderlust for all things decadent, delicious, divine, and daring! So join us on a foodie lovers' journey and let us help you find your yum!</p>
</section>

<section class="featured">
  <h2 class="title" style="top:66px">FEATURED PRODUCTS</h2>
  <div class="product" style="left:110px"><div class="img" role="img" aria-label="Black scoopneck T-shirt with cobbler print" style="background:linear-gradient(#fff,#fff 8%,#151515 9%)"></div><div class="label">SCOOPNECK T-SHIRT</div></div>
  <div class="product" style="left:358px"><div class="img" role="img" aria-label="White mug with pancakes print" style="background:radial-gradient(ellipse at 50% 55%,#f2f2f2 40%,#fff 70%)"></div><div class="label">PANCAKES MUG</div></div>
  <div class="product" style="left:607px"><div class="img" role="img" aria-label="Dark grey ladies' tank with gelato print" style="background:linear-gradient(90deg,#fff 12%,#3b3b3b 13%,#3b3b3b 87%,#fff 88%)"></div><div class="label">LADIES' TANK</div></div>
  <div class="product" style="left:855px"><div class="img" role="img" aria-label="Man wearing a grey unisex T-shirt with cobbler print" style="background:linear-gradient(#f4f4f4,#c9c9c9 40%,#b8b8b8)"></div><div class="label">UNISEX T-SHIRT</div></div>
</section>

<section class="banner" role="img" aria-label="Man in a black T-shirt with a gelato print against a moody sky">
  <p>Apparel and kitchenware to inspire while<br>you cook up and eat up!</p>
</section>

<section class="testimonials">
  <h2 class="title" style="top:103px">TESTIMONIALS</h2>
  <div class="card" style="left:110px"><div class="avatar" role="img" aria-label="Customer portrait"></div><h3>Martin Hale</h3><p>On the other hand, we denounce with righteous indignation and dislike who are beguiled and charms</p></div>
  <div class="card" style="left:443px"><div class="avatar" role="img" aria-label="Customer portrait"></div><h3>Dana Okafor</h3><p>On the other hand, we denounce with righteous indignation and dislike who are beguiled and charms</p></div>
  <div class="card" style="left:778px"><div class="avatar" role="img" aria-label="Customer portrait"></div><h3>Lena Brooks</h3><p>On the other hand, we denounce with righteous indignation and dislike who are beguiled and charms</p></div>
</section>

<section class="deal">
  <h2 class="title" style="top:62px">DEAL OF THE MONTH</h2>
  <div class="frame" style="left:110px;top:142px;width:420px;height:422px">
    <div class="photo" role="img" aria-label="Dark grey ladies' tank with gelato print" style="left:55px;top:0;width:306px;height:418px;background:linear-gradient(90deg,#fff 8%,#3a3a3a 12%,#3a3a3a 88%,#fff 92%)"></div>
  </div>
  <div class="info">
    <div style="position:absolute;top:0;white-space:nowrap">LADIES' TANK</div>
    <div style="position:absolute;top:30px;color:#555">$25</div>
    <div style="position:absolute;top:75px">SIZE</div>
    <div class="sizes"><div class="size on">SMALL</div><div class="size">MEDIUM</div><div class="size">LARGE</div></div>
    <div style="position:absolute;top:171px;white-space:nowrap">QUANTITY</div>
    <svg class="abs" style="left:0;top:212px" width="110" height="28" viewBox="0 0 110 28"><path d="M1 14h12" stroke="#444" stroke-width="3"/><rect x="27" y="2" width="49" height="24" fill="#0d57a8"/><text x="51.5" y="19" fill="#fff" font-size="13" text-anchor="middle" font-family="Open Sans,sans-serif">1</text><path d="M89 14h12M95 8v12" stroke="#444" stroke-width="2"/></svg>
    <div class="btn" style="left:0;top:269px;width:158px;height:39px;line-height:39px">ADD TO CART</div>
  </div>
</section>

<section class="news">
  <h2 class="title" style="top:100px">OUR LATEST NEWS</h2>
  <div class="frame" style="left:110px;top:175px;width:447px;height:340px">
    <div class="photo" role="img" aria-label="Golden lattice-topped apple pie mini" style="left:0;top:0;width:443px;height:336px;background:radial-gradient(circle at 45% 50%,#e2a24b,#b56a22 45%,#6b3a17 80%)"></div>
  </div>
  <div class="meta"><svg width="14" height="14" viewBox="0 0 14 14" style="vertical-align:-1px;margin-right:6px"><rect x="1" y="3" width="12" height="10" fill="none" stroke="#8a69b5" stroke-width="1.6"/><path d="M1 6h12M4 1v3M10 1v3" stroke="#8a69b5" stroke-width="1.6"/></svg>April 14, 2019</div>
  <p>Dearly Beloved, we are gathered here today to celebrate the union of salted caramel sauce and warm spiced apples. I present to you a recipe for a dessert marriage made in heaven: Salted Caramel Apple Pie Minis. Enjoy!</p>
  <div class="btn" style="left:650px;top:418px;width:117px;height:38px;line-height:38px">READ MORE</div>
</section>

<section class="subscribe">
  <h2>SUBSCRIBE TO OUR<br>NEWSLETTER:</h2>
  <div class="sub-input"><svg width="13" height="10" viewBox="0 0 13 10" style="margin-right:6px"><rect x=".7" y=".7" width="11.6" height="8.6" fill="none" stroke="#999" stroke-width="1.3"/><path d="M1 1l5.5 4.5L12 1" fill="none" stroke="#999" stroke-width="1.3"/></svg>Enter Your Email</div>
  <div class="btn" style="left:956px;top:100px;width:132px;height:42px;line-height:42px">SUBSCRIBE</div>
</section>

<footer class="footer">
  <h4 style="left:112px">ABOUT THE SHOP</h4>
  <div class="txt" style="left:112px;top:112px;width:260px;line-height:26px">Apparel and kitchenware to inspire while you cook up and eat up!</div>
  <div class="abs" style="left:112px;top:194px">
    <span class="pay" style="background:#3b5fa8"></span><span class="pay" style="background:#d9822b"></span><span class="pay" style="background:#e6e6e6"></span><span class="pay" style="background:#4a8fcf"></span>
  </div>
  <div class="txt" style="left:112px;top:244px">© 2019 Savorly.All rights Reserved</div>

  <h4 style="left:413px">FOOTER MENU</h4>
  <div class="txt" style="left:413px;top:110px">HOME<br>SHOP<br>ABOUT US<br>Log in<br>Create account<br>Products<br>About Us</div>

  <h4 style="left:614px">CONTACT US</h4>
  <div class="field" style="top:116px;height:37px">Enter Your Name</div>
  <div class="field" style="top:166px;height:37px">Enter Your Email</div>
  <div class="field" style="top:214px;height:37px">Enter Your Phone Number</div>
  <div class="field" style="top:262px;height:80px">Enter Your Message</div>
  <div class="btn" style="left:614px;top:360px;width:80px;height:27px;line-height:27px;font-size:13px">SEND</div>

  <h4 style="left:988px">FOLLOW US</h4>
  <div class="social" style="top:115px"><i></i>Pagebook</div>
  <div class="social" style="top:158px"><i></i>Photogram</div>
  <div class="social" style="top:200px"><i></i>Chirpline</div>
  <div class="social" style="top:243px"><i></i>Clipcast</div>
</footer>

</body>
</html>
```